Maple Lantern Productions web site

I need to build a website for a new company I am launching next month. Maple Lantern Productions is a company based in New England that provides sound, lighting, and audio visual services to weddings, corporate, and any other cusomer base looking for quality service for a fair price. Looking for somebody to do a full site not just the image files. I am looking to keep the colors of my logo (orange and black) and possibly grey and white. I am looking to build my site very similar to brightvaleevents.example, which is owned by a friend of mine. I like how he has the big pictures that load in to the site and the basic menu items. I'll need a gallery of photos. The designs should communicate quality, value and trust.
My website address is maplelanternco.example.
Updates

Hi and thanks to everyone for posting such great ideas for our new design.I have some items that I'd like to ask you all to focus on in your revisions.I like how http://www.brightvaleevents.example/ website has five or six high res pictures that change in a slideshow format with a caption that loads in for each one for the different types of services. Try and capture pics like these and with teh same headings as he has. The basic menu designs have been interesting.I am more fond of the menus that are more white with some orange as I dont want it to be too dark. I'm curious to see how your galleries will work and if i'll be able to edit the pages myself? I have some more info on the company for you to fill in:website address is ciderhouseco.comemail: info@ciderhouseco.comaddress: Maple Lantern Productions57 Littlefield StreetAvon, MA 02417"New England's finest DJ's, lighting and sound, video and more. Creating memories one perfect event at a time."Put this under the loading pictures as a tagline.About Cider HouseCider House Productions is a collection of New England's finest talent, ready to make your next event the one you've dreamed of. We have the skills and expertise to deliver your vision of your perfect event. From elegant weddings to themed mitzvah's, corporate av, videography and detail lighting, we offer all of the elements to make your event a success. Added Wednesday, March 1, 2017

Designer's Please also make sure that your design flows well on any device it is being viewed on as well. Thanks. Added Wednesday, March 1, 2017

Project Deadline Extended Reason: Hello designerThank you all very much for your hard work on our project. Im sorry but i need to extend the date of my project. Our parent conpany Rook Nine Prodactions sponsors Bay Youth Assemblies and we are currently at their leadership conference on the Cape. I will be back in on Monday and with your help will get this finished by Thursday the 16th. Thanks Added Thursday, March 9, 2017

Project Deadline Extended Reason: One of the designers is not responding so I now have to make revisions with other designers. I hope to get this website done over the weekends so please get your revisions as soon as possible. Thank you. I am also upgrading the budget another $75 to hopefully get some more interest on my project. Added Wednesday, March 15, 2017

Target Market(s)

Wedding - Corporate -

Industry/Entity Type

It Company

Coding

Coded - Design and coding required

Number of Pages Required

5+ page

Font styles to use
Sans Serif

Requirements
Must have
• Photo Gallery - I want to be able to edit it myself
Nice to have
• I like the look of my friends website brightvaleevents.example

```html
<!DOCTYPE html>
<html lang="en">
<head>
<meta charset="utf-8">
<title>Maple Lantern Productions</title>
<link href="https://fonts.googleapis.com/css2?family=Roboto:wght@300;400;500;700&family=Raleway:wght@600;700&display=swap" rel="stylesheet">
<style>
:root{
  --orange:#f26b2a;
  --orange-dark:#e05a1c;
  --ink:#2b2b2b;
  --text:#666;
  --light:#f4f4f4;
  --line:#e3e3e3;
  --white:#fff;
  --dark:#2e2e2e;
}
*{box-sizing:border-box;margin:0;padding:0}
html,body{width:1200px;height:3442px;overflow:hidden}
body{font-family:'Roboto',sans-serif;color:var(--text);background:var(--white);position:relative}
.abs{position:absolute}
p{font-size:12.5px;line-height:26px}

/* header */
.site-header{left:0;top:0;width:1200px;height:87px;background:var(--white)}
.brand{left:86px;top:18px;display:flex;align-items:center;gap:12px}
.brand-dot{width:50px;height:50px;border-radius:50%;background:var(--orange)}
.brand-name{font-family:'Raleway',sans-serif;font-weight:700;font-size:20px;line-height:22px;color:var(--ink);letter-spacing:.5px;text-transform:uppercase;width:170px}
.main-nav{left:506px;top:0;height:87px;display:flex;align-items:center;gap:0}
.main-nav a{font-size:12px;font-weight:500;color:var(--ink);text-decoration:none;text-transform:uppercase;padding:0 23px}
.main-nav a.active{color:var(--orange)}
.search-btn{left:1068px;top:21px;width:46px;height:46px;border-radius:50%;background:var(--orange)}

/* hero */
.hero{left:0;top:87px;width:1200px;height:503px;background:linear-gradient(100deg,#6d7256 0%,#b7ad99 30%,#e7dfd4 45%,#a79c8c 65%,#7b7a73 100%)}
.hero-arrow{top:215px;width:52px;height:52px;border:2px solid rgba(255,255,255,.9);border-radius:50%}
.hero-arrow.prev{left:24px}
.hero-arrow.next{left:1122px}
.hero-caption{left:706px;top:305px;width:420px}
.hero-caption h1{font-weight:300;font-size:52px;color:var(--orange);text-transform:uppercase;line-height:60px}
.hero-caption p{color:var(--white);font-size:12.5px;line-height:26px;margin-top:6px}

/* buttons */
.btn{display:inline-block;background:var(--orange);color:var(--white);font-size:12px;font-weight:500;text-transform:uppercase;text-decoration:none;padding:0 20px;height:42px;line-height:42px;border-radius:3px}
.btn-ghost{background:transparent;border:1px solid var(--white);font-weight:400}

/* section titles */
.section-title{width:1200px;left:0;text-align:center;font-weight:300;font-size:25px;color:var(--ink);text-transform:uppercase}
.section-title span{color:var(--orange)}
.section-sub{width:1200px;left:0;text-align:center;font-size:12.5px}

/* welcome */
.welcome-text{left:270px;top:676px;width:660px;text-align:center}

/* services */
.services{left:0;top:860px;width:1200px;height:1441px;background:var(--light)}
.service-photo{width:418px;height:255px;border-radius:4px}
.service-title{font-family:'Raleway',sans-serif;font-weight:700;font-size:16px;color:var(--ink);text-transform:uppercase}
.service-rule{width:56px;height:3px;background:var(--orange)}
.service-text{width:500px}
.divider{left:90px;width:1020px;height:1px;background:var(--line)}

/* about band */
.about-band{left:0;top:2301px;width:1200px;height:278px;background:linear-gradient(90deg,var(--orange-dark),var(--orange) 50%,var(--orange-dark))}
.about-band h2{position:absolute;top:45px;width:1200px;text-align:center;font-weight:300;font-size:25px;color:var(--white)}
.about-band p{position:absolute;top:86px;left:240px;width:720px;text-align:center;color:var(--white)}

/* gallery */
.gallery-tile{border-radius:2px}

/* footer */
.site-footer{left:0;top:3095px;width:1200px;height:277px;background:var(--light)}
.footer-brand{left:110px;top:58px;width:240px;text-align:center}
.footer-brand .brand-dot{width:92px;height:92px;margin:0 auto 14px}
.footer-brand .brand-name{width:240px;font-size:26px;line-height:30px}
.footer-col h4{font-size:15px;font-weight:500;color:var(--ink);text-transform:uppercase;letter-spacing:.5px}
.contact-list{list-style:none;margin-top:22px}
.contact-list li{display:flex;align-items:flex-start;gap:12px;font-size:12px;line-height:15px;margin-bottom:14px;color:#555}
.contact-list a{color:#555}
.contact-list svg{flex:none}
.newsletter p{font-size:12.5px;line-height:20px;margin-top:20px;color:#555}
.email-field{margin-top:14px;width:212px;height:34px;border:1px solid #ddd;background:var(--white);font-size:11px;padding-left:10px;line-height:32px;color:#777}
.subscribe{margin-top:16px;height:26px;line-height:26px;font-size:10px;padding:0 10px;border-radius:2px}
.follow p{font-size:11.5px;line-height:18px;margin-top:20px;color:#555}
.socials{display:flex;gap:10px;margin-top:18px}
.socials span{width:34px;height:34px;border-radius:50%;border:1.5px solid #bbb}
.copyright{left:0;top:3372px;width:1200px;height:70px;background:var(--dark);color:#ddd;font-size:12px;text-align:center;line-height:70px}
</style>
</head>
<body>

<header class="site-header abs">
  <div class="brand abs">
    <span class="brand-dot"></span>
    <span class="brand-name">Maple Lantern Productions</span>
  </div>
  <nav class="main-nav abs">
    <a class="active" href="#">Home</a>
    <a href="#">About Us</a>
    <a href="#">Services</a>
    <a href="#">Events</a>
    <a href="#">Gallery</a>
    <a href="#">Contact Us</a>
  </nav>
  <span class="search-btn abs">
    <svg width="46" height="46" viewBox="0 0 46 46"><circle cx="21" cy="21" r="5" fill="none" stroke="#fff" stroke-width="2"/><line x1="25" y1="25" x2="29" y2="29" stroke="#fff" stroke-width="2.2" stroke-linecap="round"/></svg>
  </span>
</header>

<section class="hero abs" role="img" aria-label="Slideshow photo of a smiling wedding couple embracing outdoors">
  <span class="hero-arrow prev abs"><svg width="48" height="48" viewBox="0 0 48 48"><polyline points="27,17 20,24 27,31" fill="none" stroke="#fff" stroke-width="2.5"/></svg></span>
  <span class="hero-arrow next abs"><svg width="48" height="48" viewBox="0 0 48 48"><polyline points="21,17 28,24 21,31" fill="none" stroke="#fff" stroke-width="2.5"/></svg></span>
  <div class="hero-caption abs">
    <h1>Maple Lantern</h1>
    <p>Sed ut perspiciatis unde omnis iste natus error sit voluptatem accusantium doloremque laudantium, totam rem aperiam, eaque ipsa quae ab illo inventore veritatis et quasi architecto beatae vitae dicta sunt explicabo.</p>
  </div>
</section>

<section class="welcome">
  <h2 class="section-title abs" style="top:630px">Welcome to <span>Maple Lantern Productions</span></h2>
  <p class="welcome-text abs">Sed ut perspiciatis unde omnis iste natus error sit voluptatem accusantium doloremque laudantium, totam rem aperiam, eaque ipsa quae ab illo inventore veritatis et quasi architecto beatae vitae dicta sunt explicabo. Nemo enim ipsam aut consequuntur magni dolores eos qui ratione voluptatem sequi nesciunt</p>
  <a class="btn abs" href="#" style="left:519px;top:773px;width:162px;text-align:center">Read More Info</a>
</section>

<section class="services abs">
  <h2 class="section-title abs" style="top:30px">Our <span>Services</span></h2>
  <p class="section-sub abs" style="top:68px">Sed ut perspiciatis unde omnis iste natus error sit voluptatem accusantium doloremque laudantium.</p>

  <div class="service-photo abs" style="left:103px;top:136px;background:linear-gradient(180deg,#6a4a2c,#c08a4a 45%,#2a2a30)" role="img" aria-label="Stage with performers above a sound mixing desk"></div>
  <h3 class="service-title abs" style="left:583px;top:146px">Sound Services</h3>
  <span class="service-rule abs" style="left:583px;top:178px"></span>
  <p class="service-text abs" style="left:583px;top:202px">Sed ut perspiciatis unde omnis iste natus error sit voluptatem accusantium doloremque laudantium, totam rem aperiam, eaque ipsa quae ab illo inventore veritatis et quasi architecto beatae vitae dicta sunt explicabo. Nemo enim ipsam voluptatem quia voluptas sit aspernatur la consequuntur magni dolores eos qui ratione voluptatem sequi nesciunt.</p>
  <a class="btn abs" href="#" style="left:585px;top:326px">Read More Info</a>

  <span class="divider abs" style="top:432px"></span>

  <h3 class="service-title abs" style="left:103px;top:484px">Lighting Services</h3>
  <span class="service-rule abs" style="left:103px;top:516px"></span>
  <p class="service-text abs" style="left:103px;top:540px">Sed ut perspiciatis unde omnis iste natus error sit voluptatem accusantium doloremque laudantium, totam rem aperiam, eaque ipsa quae ab illo inventore veritatis et quasi architecto beatae vitae dicta sunt explicabo. Nemo enim ipsam voluptatem quia voluptas sit aspernatur la consequuntur magni dolores eos qui ratione voluptatem sequi nesciunt.</p>
  <a class="btn abs" href="#" style="left:105px;top:664px">Read More Info</a>
  <div class="service-photo abs" style="left:679px;top:470px;background:linear-gradient(180deg,#b68fd8,#6c3bb0 55%,#3a1c6e)" role="img" aria-label="Banquet hall lit in purple with draped ceiling"></div>

  <div class="service-photo abs" style="left:103px;top:805px;background:linear-gradient(180deg,#2a3e6a,#5a7fc0 40%,#1a1a1f)" role="img" aria-label="DJ controller and laptop in front of a crowd"></div>
  <h3 class="service-title abs" style="left:583px;top:815px">Audio Services</h3>
  <span class="service-rule abs" style="left:583px;top:847px"></span>
  <p class="service-text abs" style="left:583px;top:871px">Sed ut perspiciatis unde omnis iste natus error sit voluptatem accusantium doloremque laudantium, totam rem aperiam, eaque ipsa quae ab illo inventore veritatis et quasi architecto beatae vitae dicta sunt explicabo. Nemo enim ipsam voluptatem quia voluptas sit aspernatur la consequuntur magni dolores eos qui ratione voluptatem sequi nesciunt.</p>
  <a class="btn abs" href="#" style="left:585px;top:995px">Read More Info</a>

  <span class="divider abs" style="top:1101px"></span>

  <h3 class="service-title abs" style="left:103px;top:1153px">Visual Services</h3>
  <span class="service-rule abs" style="left:103px;top:1185px"></span>
  <p class="service-text abs" style="left:103px;top:1209px">Sed ut perspiciatis unde omnis iste natus error sit voluptatem accusantium doloremque laudantium, totam rem aperiam, eaque ipsa quae ab illo inventore veritatis et quasi architecto beatae vitae dicta sunt explicabo. Nemo enim ipsam voluptatem quia voluptas sit aspernatur la consequuntur magni dolores eos qui ratione voluptatem sequi nesciunt.</p>
  <a class="btn abs" href="#" style="left:105px;top:1333px">Read More Info</a>
  <div class="service-photo abs" style="left:679px;top:1140px;background:linear-gradient(135deg,#4a4038,#b9a592 45%,#6e6660)" role="img" aria-label="Collage of wedding photographs"></div>
</section>

<section class="about-band abs">
  <h2>ABOUT US</h2>
  <p>Sed ut perspiciatis unde omnis iste natus error sit voluptatem accusantium doloremque laudantium, totam rem aperiam, eaque ipsa quae ab illo inventore veritatis et quasi architecto beatae vitae dicta sunt explicabo. Nemo enim ipsam voluptatem quia voluptas sit sed quia consequuntur magni dolores eos qui ratione voluptatem sequi nesciunt.</p>
  <a class="btn btn-ghost abs" href="#" style="left:486px;top:190px;width:225px;text-align:center">Click Here For More Info</a>
</section>

<section class="gallery">
  <h2 class="section-title abs" style="top:2617px">Photo <span>Gallery</span></h2>
  <p class="section-sub abs" style="top:2656px">Sed ut perspiciatis unde omnis iste natus error sit voluptatem accusantium doloremque laudantium.</p>
  <div class="gallery-tile abs" style="left:87px;top:2700px;width:505px;height:165px;background:linear-gradient(90deg,#1c2140,#6a5a8a 50%,#1c2140)" role="img" aria-label="Couple dancing between sparkler fountains"></div>
  <div class="gallery-tile abs" style="left:603px;top:2700px;width:250px;height:342px;background:linear-gradient(180deg,#2a3020,#8a8a3a 50%,#4a4a3a)" role="img" aria-label="Outdoor aisle under an arch of string lights"></div>
  <div class="gallery-tile abs" style="left:865px;top:2700px;width:248px;height:165px;background:linear-gradient(180deg,#3a2a1a,#c8a070 55%,#e8dccc)" role="img" aria-label="Reception tables under string lights"></div>
  <div class="gallery-tile abs" style="left:87px;top:2874px;width:250px;height:168px;background:linear-gradient(180deg,#6a4a2c,#c08a4a 45%,#2a2a30)" role="img" aria-label="Stage and sound desk"></div>
  <div class="gallery-tile abs" style="left:346px;top:2874px;width:246px;height:168px;background:linear-gradient(135deg,#2a2420,#8a6a4a 55%,#3a302a)" role="img" aria-label="Musician playing acoustic guitar"></div>
  <div class="gallery-tile abs" style="left:865px;top:2874px;width:248px;height:168px;background:linear-gradient(135deg,#1e1e20,#6a6460 50%,#b08a40)" role="img" aria-label="Saxophone player in a suit"></div>
</section>

<footer class="site-footer abs">
  <div class="footer-brand abs">
    <span class="brand-dot" style="display:block"></span>
    <span class="brand-name" style="display:block">Maple Lantern Productions</span>
  </div>

  <div class="footer-col abs" style="left:406px;top:52px;width:220px">
    <h4>Contact Us</h4>
    <ul class="contact-list">
      <li><svg width="14" height="14" viewBox="0 0 14 14"><path d="M3 1h3l1 3-2 1a8 8 0 0 0 4 4l1-2 3 1v3a1 1 0 0 1-1 1A11 11 0 0 1 2 2a1 1 0 0 1 1-1z" fill="#777"/></svg>(000)-121-1231 (Phone)</li>
      <li><svg width="14" height="14" viewBox="0 0 14 14"><rect x="2" y="5" width="10" height="7" fill="#777"/><rect x="4" y="1" width="6" height="4" fill="none" stroke="#777"/></svg>(000)-121-1231 (Fax)</li>
      <li><svg width="14" height="14" viewBox="0 0 14 14"><rect x="1" y="3" width="12" height="8" fill="none" stroke="#777"/><polyline points="1,3 7,8 13,3" fill="none" stroke="#777"/></svg><a href="#">info@maplelanternco.example</a></li>
      <li><svg width="14" height="14" viewBox="0 0 14 14"><path d="M7 1a4 4 0 0 1 4 4c0 3-4 8-4 8S3 8 3 5a4 4 0 0 1 4-4z" fill="#777"/><circle cx="7" cy="5" r="1.5" fill="#f4f4f4"/></svg>#24 Lorem Ipsum Dummy<br>Lorem Ipsum</li>
    </ul>
  </div>

  <div class="footer-col newsletter abs" style="left:649px;top:52px;width:220px">
    <h4>Newsletter</h4>
    <p>Register Your email address to get information ablout us</p>
    <div class="email-field">Email Address</div>
    <a class="btn subscribe" href="#">Subscribe</a>
  </div>

  <div class="footer-col follow abs" style="left:906px;top:52px;width:200px">
    <h4>Follow Us</h4>
    <p>Lorem ipsum dolor sit amet, conse ctetur adipiscing elit. Nulla in purus nibh. Donec ornare</p>
    <div class="socials"><span></span><span></span><span></span><span></span><span></span></div>
  </div>
</footer>

<div class="copyright abs">© Copyright 2017 Maple Lantern co.All Rights Reserved</div>

</body>
</html>
```